Small Business Consulting Firm Needs Letterhead

We need a letterhead for our company "Brightpath Plus". Our company does outbound calling and mailing to business owner's companies who have taken high interest loans. These loans tend to put these businesses in a big financial bind short term, and we help them find better financial options. We would like the design to match our colors of our logo. Headers and footers would look nice, but we are open. We would want it to include our address, website, phone, and email info. Our address - 2000 E. Lamar Blvd. Suite 600Website - www.safeguardtoday.comEmail - info@safeguardtoday.comPhone - 855-726-1938
Industry/Entity Type
Financial Planning
Look and feel
Each slider illustrates characteristics of the customer's brand and the style your logo design should communicate.

```html
<!DOCTYPE html>
<html lang="en">
<head>
<meta charset="utf-8">
<title>Brightpath Plus Letterhead</title>
<link href="https://fonts.googleapis.com/css2?family=Open+Sans:wght@400&family=Roboto:wght@400&display=swap" rel="stylesheet">
<style>
  :root {
    --backdrop: #e6dfdb;
    --paper: #f6f6f6;
    --ink: #545454;
    --brand-blue: #0a77bd;
    --brand-green: #6bb33d;
    --signature-tone: #2a2a2a;
  }
  * { box-sizing: border-box; margin: 0; padding: 0; }
  html, body {
    width: 1200px; height: 1108px; overflow: hidden;
    background: var(--backdrop);
  }
  .letterhead {
    position: absolute; left: 226px; top: 24px;
    width: 747px; height: 1060px;
    background: var(--paper);
    box-shadow: 0 2px 10px rgba(0,0,0,0.12);
    color: var(--ink);
    font-family: "Open Sans", sans-serif;
  }
  .brand {
    position: absolute; left: 66px; top: 120px;
    display: flex; align-items: center; gap: 9px;
  }
  .brand-square {
    width: 16px; height: 16px; background: var(--brand-green);
  }
  .brand-name {
    font-size: 16px; letter-spacing: 0.06em; color: var(--ink);
    font-weight: 400; text-transform: uppercase;
  }
  .contact {
    position: absolute; right: 68px; top: 70px;
    list-style: none;
    font-family: "Roboto", sans-serif; font-size: 14px; line-height: 18.5px;
    text-align: right;
  }
  .contact li { display: flex; justify-content: flex-end; align-items: center; gap: 5px; }
  .contact svg { width: 12px; height: 12px; fill: var(--brand-green); flex: none; }
  .letter-body {
    position: absolute; left: 67px; top: 279px; width: 611px;
    font-size: 13.2px; line-height: 20.1px;
  }
  .letter-body p { margin-bottom: 20.1px; text-align: justify; }
  .letter-body .salutation, .letter-body .closing { text-align: left; }
  .letter-body .closing { margin-bottom: 16px; }
  .signature {
    width: 84px; height: 80px;
    background: linear-gradient(135deg, rgba(42,42,42,0.10), rgba(42,42,42,0.04));
  }
  .footer-band {
    position: absolute; left: 0; bottom: 0; width: 747px; height: 25px; display: block;
  }
</style>
</head>
<body>
  <main class="letterhead">
    <header>
      <div class="brand">
        <span class="brand-square"></span>
        <span class="brand-name">Brightpath Plus</span>
      </div>
      <ul class="contact">
        <li>855-726-1938
          <svg viewBox="0 0 12 12"><path d="M2.4 0.8l2 2.1-1 1.3c.6 1.5 1.8 2.7 3.3 3.3l1.3-1 2.1 2-1.2 1.9C5 10.2 1.7 6.9 0.5 2z"/></svg>
        </li>
        <li>info@brightpathplus.com
          <svg viewBox="0 0 12 12"><path d="M0.5 2.5h11v7h-11z M1 3l5 3.6L11 3" stroke="#f6f6f6" stroke-width="0.9"/></svg>
        </li>
        <li>www.brightpathplus.com
          <svg viewBox="0 0 12 12"><circle cx="6" cy="6" r="5.5"/><path d="M3 3.5l2 .5 .5 2-1.5 1 .5 2.5M8 2.5l-.5 2 1.5 1.5 1-.5" stroke="#f6f6f6" stroke-width="0.9" fill="none"/></svg>
        </li>
        <li>4170 W. Corwin Ave. Suite 310
          <svg viewBox="0 0 12 12"><path d="M6 0.3a4 4 0 0 1 4 4c0 3-4 7.4-4 7.4S2 7.3 2 4.3a4 4 0 0 1 4-4z M6 2.6a1.7 1.7 0 1 0 0 3.4 1.7 1.7 0 1 0 0-3.4z" fill-rule="evenodd"/></svg>
        </li>
      </ul>
    </header>

    <section class="letter-body">
      <p class="salutation">Dear customer,</p>
      <p>Lorem ipsum dolor sit amet, consectetur adipisicing elit, sed do eiusmod tempor incididunt ut labore et dolore magna aliqua. Ut enim ad minim veniam, quis nostrud exercitation ullamco laboris nisi ut aliquip ex ea commodo consequat. Duis aute irure dolor in reprehenderit in voluptate velit esse cillum dolore eu fugiat nulla pariatur. Excepteur sint occaecat cupidatat non proident, sunt in culpa qui officia deserunt mollit anim id est laborum.</p>
      <p>Lorem ipsum dolor sit amet, consectetur adipisicing elit, sed do eiusmod tempor incididunt ut labore et dolore magna aliqua. Ut enim ad minim veniam, quis nostrud exercitation ullamco laboris nisi ut aliquip ex ea commodo consequat. Duis aute irure dolor in reprehenderit in voluptate velit esse cillum dolore eu fugiat nulla pariatur. Excepteur sint occaecat cupidatat non proident, sunt in culpa qui officia deserunt mollit anim id est laborum.</p>
      <p>Lorem ipsum dolor sit amet, consectetur adipisicing elit, sed do eiusmod tempor incididunt ut labore et dolore magna aliqua. Ut enim ad minim veniam, quis nostrud exercitation ullamco laboris nisi ut aliquip ex ea commodo consequat. Duis aute irure dolor in reprehenderit in voluptate velit esse cillum dolore eu fugiat nulla pariatur. Excepteur sint occaecat cupidatat non proident, sunt in culpa qui officia deserunt mollit anim id est laborum.</p>
      <p>Lorem ipsum dolor sit amet, consectetur adipisicing elit, sed do eiusmod tempor incididunt ut labore et dolore magna aliqua. Ut enim ad minim veniam, quis nostrud exercitation ullamco laboris nisi ut aliquip ex ea commodo consequat. Duis aute irure dolor in reprehenderit.</p>
      <p class="closing">Yours Sincerely,</p>
      <div class="signature" role="img" aria-label="Handwritten signature of the sender"></div>
    </section>

    <svg class="footer-band" viewBox="0 0 747 25" aria-hidden="true">
      <polygon points="0,10 483,10 475,25 0,25" fill="var(--brand-blue)"/>
      <polygon points="496,0 747,0 747,25 485,25" fill="var(--brand-green)"/>
    </svg>
  </main>
</body>
</html>
```